Web design for Money Service Business (uncoded)

We need a very basic website with 5-6 pages. Home page, Services, Transfer(How to use our service), About us, Contact us, FAQ
Our company name is Norvane Exchange. We are a company that deals with currency exchange and international money transfer. We do cash exchange and international money transfers to bank accounts all over the world. We offer highly competitive exchange rates so usually attract customers who transfer money over $10,000. Our niche is with larger sums of money, the design needs to be professional and communicate trust, security and stability.

```html
<!DOCTYPE html>
<html lang="en">
<head>
<meta charset="utf-8">
<title>Norvane Exchange — International Money Transfer</title>
<link href="https://fonts.googleapis.com/css2?family=Open+Sans:ital,wght@0,400;0,600;0,700;1,400&family=Noto+Serif:wght@400&display=swap" rel="stylesheet">
<style>
:root{
  --navy:#0c3b6e;
  --navy-dark:#092f59;
  --orange:#f39a1e;
  --heading:#15467e;
  --text:#444;
  --muted:#777;
  --page-bg:#ebebeb;
  --white:#fff;
  --rule:#c9c9c9;
}
*{margin:0;padding:0;box-sizing:border-box}
html,body{width:738px;height:1200px;overflow:hidden}
body{background:var(--page-bg);font-family:"Open Sans",Arial,sans-serif;color:var(--text);position:relative}
.site{position:absolute;left:62px;top:0;width:615px;height:1200px;background:var(--white);box-shadow:0 0 3px rgba(0,0,0,.15)}
.abs{position:absolute}
.topbar{left:0;top:0;width:615px;height:29px;background:var(--navy);color:var(--white);font-size:9px}
.topbar .date{left:14px;top:9px}
.topbar .phone{right:13px;top:9px;display:flex;align-items:center;gap:4px}
.logo{left:15px;top:54px;display:flex;align-items:center;gap:5px;font-weight:700;font-size:14px;color:var(--navy);letter-spacing:.2px}
.logo .mark{width:9px;height:9px;background:var(--orange)}
.nav{left:0;top:29px;height:69px;width:615px}
.nav a{position:absolute;top:0;height:69px;line-height:69px;font-size:9px;color:#555;text-decoration:none;text-transform:uppercase;transform:translateX(-50%)}
.nav a.active{background:var(--navy);color:var(--white);width:60px;text-align:center;transform:none;left:228px}
.hero{left:0;top:98px;width:615px;height:217px;background:radial-gradient(ellipse at 65% 55%,#a9ad96 0%,#7d806c 35%,#4a4b40 70%,#2b2b27 100%)}
.caption{left:13px;color:var(--white);font-weight:600;font-size:11px;padding:0 10px;line-height:25px;white-space:nowrap}
.caption.one{top:68px;height:26px;background:rgba(12,59,110,.75)}
.caption.two{top:96px;height:25px;background:rgba(243,154,30,.85)}
.hero .btn{left:13px;top:123px;width:94px;height:22px;background:var(--navy);color:var(--white);font-size:8.5px;text-align:center;line-height:22px}
.dots{right:16px;top:203px;display:flex;gap:2px}
.dots span{width:6px;height:6px;background:var(--white)}
.dots span:first-child{background:var(--orange)}
.section-title{left:12px;width:591px;display:flex;align-items:center;gap:9px;font-family:"Noto Serif",Georgia,serif;font-size:15.5px;color:var(--heading);white-space:nowrap;font-weight:400}
.rule{flex:1;height:8px;background:repeating-linear-gradient(90deg,var(--rule) 0 1px,transparent 1px 2px)}
.photo{display:block}
.service h3,.welcome h2,.news h4{font-weight:400}
.service h3{font-family:"Noto Serif",Georgia,serif;font-size:12px;color:var(--heading)}
.service p{font-size:7px;line-height:10.8px;color:var(--text);margin-top:6px;width:140px}
.pill{display:inline-block;background:var(--orange);color:#3a2a10;font-size:7px;padding:0 9px;height:15px;line-height:15px;border-radius:2px;margin-top:7px}
.welcome h2{font-family:"Noto Serif",Georgia,serif;font-size:14px;color:var(--heading)}
.welcome h2 em{font-style:normal;color:var(--orange)}
.welcome .sub{font-family:"Noto Serif",Georgia,serif;font-size:8.5px;margin:5px 0 0 3px;color:#333}
.welcome p{font-size:7px;line-height:12px;margin:7px 0 0 3px;width:413px}
.quote{font-style:italic;font-size:9.5px;line-height:12.9px;color:var(--muted);width:190px}
.disc-text{font-size:7px;line-height:15px;width:205px}
.btn-navy{background:var(--navy);color:var(--white);font-size:8.5px;border-radius:3px;text-align:center;line-height:18px}
.news h4{font-size:8.8px;font-weight:600;color:#333}
.news .meta{font-size:7px;color:var(--navy);margin-top:1px}
.news .meta.alt{color:var(--orange)}
.news p{font-size:7px;margin-top:4px;line-height:11px}
.news .more{color:var(--navy)}
.news .more.alt{color:var(--orange)}
.news-icon{width:30px;height:44px;display:flex;align-items:center;justify-content:center}
.footer{left:0;top:1126px;width:615px;height:74px;background:var(--navy);color:var(--white);font-size:7.5px}
.footer .links{left:13px;top:24px;display:flex;gap:12px;text-transform:uppercase}
.footer .copy{left:13px;top:47px}
.footer .legal{right:13px;top:47px;display:flex;gap:16px}
.socials{right:13px;top:19px;display:flex;gap:4px}
.socials span{width:13px;height:13px;border-radius:2px}
</style>
</head>
<body>
<div class="site">
  <div class="abs topbar">
    <span class="abs date">November 29th, 2013</span>
    <span class="abs phone">
      <svg width="9" height="9" viewBox="0 0 24 24"><path fill="#fff" d="M6.6 10.8c1.4 2.8 3.8 5.1 6.6 6.6l2.2-2.2c.3-.3.7-.4 1-.2 1.1.4 2.3.6 3.6.6.6 0 1 .4 1 1V20c0 .6-.4 1-1 1C10.6 21 3 13.4 3 4c0-.6.4-1 1-1h3.5c.6 0 1 .4 1 1 0 1.3.2 2.5.6 3.6.1.3 0 .7-.2 1z"/></svg>
      0800-555-0192
    </span>
  </div>

  <nav class="abs nav">
    <div class="abs logo" style="top:25px"><span class="mark"></span>Norvane Exchange</div>
    <a class="active" href="#">Home</a>
    <a href="#" style="left:328px">About Us</a>
    <a href="#" style="left:411px">Portfolio</a>
    <a href="#" style="left:491px">Services</a>
    <a href="#" style="left:567px">Contact</a>
  </nav>

  <section class="abs hero" role="img" aria-label="Pile of US dollar banknotes">
    <div class="abs caption one">THE NORVANE EXCHANGE INTERNATIONAL MONEY TRANSFER</div>
    <div class="abs caption two">ENSURE THE MONEY TRANSFER IN SAVE HANDS</div>
    <div class="abs btn">READ MORE</div>
    <div class="abs dots"><span></span><span></span><span></span><span></span></div>
  </section>

  <h2 class="abs section-title" style="top:340px"><span class="rule"></span>Our Services<span class="rule"></span></h2>

  <div class="abs service" style="left:12px;top:382px;display:flex;gap:14px">
    <div class="photo" role="img" aria-label="Fanned foreign currency notes" style="width:121px;height:76px;background:linear-gradient(135deg,#6b7a5a,#b9a77a 50%,#4f5a48)"></div>
    <div><h3>Currency Exchange</h3><p>Lorem Ipsum est simplement du faux exte mployé dans la sition et la misen page avant impression...</p><span class="pill">READ MORE</span></div>
  </div>
  <div class="abs service" style="left:323px;top:382px;display:flex;gap:18px">
    <div class="photo" role="img" aria-label="Cash to card kiosk machine" style="width:121px;height:76px;background:linear-gradient(90deg,#5a4630,#c7b89c 40%,#9a7a4c 70%,#5c4328)"></div>
    <div><h3>Cash To Card</h3><p>Lorem Ipsum est simplement du faux exte mployé dans la sition et la misen page avant impression...</p><span class="pill">READ MORE</span></div>
  </div>
  <div class="abs service" style="left:12px;top:487px;display:flex;gap:13px">
    <div class="photo" role="img" aria-label="Assorted world banknotes" style="width:121px;height:76px;background:linear-gradient(135deg,#3a4a5a,#c4866a 45%,#7c8c5c 70%,#2f2f2f)"></div>
    <div><h3>Mobile Money Transfer</h3><p>Lorem Ipsum est simplement du faux exte mployé dans la sition et la misen page avant impression...</p><span class="pill">READ MORE</span></div>
  </div>
  <div class="abs service" style="left:323px;top:487px;display:flex;gap:18px">
    <div class="photo" role="img" aria-label="Man working at a laptop" style="width:121px;height:76px;background:linear-gradient(135deg,#8a7a60,#d8d0bf 45%,#3a3a3a)"></div>
    <div><h3>Online Money Transfer</h3><p>Lorem Ipsum est simplement du faux exte mployé dans la sition et la misen page avant impression...</p><span class="pill">READ MORE</span></div>
  </div>

  <section class="abs welcome" style="left:12px;top:615px;display:flex;gap:11px">
    <div class="photo" role="img" aria-label="Heap of mixed currency notes on a dark background" style="width:165px;height:108px;background:radial-gradient(ellipse at 50% 65%,#c8a98a,#8a6a5a 45%,#2a2a4a 85%)"></div>
    <div><h2>Welcome to the <em>Norvane Exchange</em></h2>
      <div class="sub">International Money Transfer</div>
      <p>Lorem Ipsum est simplement du faux texte employé dans la sition et la misen page avant impression. Le Lorem Ipsum est le faux texte standard de l'imprimerie depuis les années 1500, quand un peintre anonyme assembla ensemble des morceaux de texte pour réaliser un livre spécimen de polices de texte.</p>
      <p style="margin-top:12px">Il n'a pas fait que survivre cinq siècles, mais s'est aussi adapté à la bureautique informatique, sans que son contenu n'en soit modifié. Il a été popularisé dans les années 1960...</p>
    </div>
  </section>

  <h2 class="abs section-title" style="left:20px;width:284px;top:768px">Testimonial<span class="rule"></span></h2>
  <div class="abs" role="img" aria-label="Portrait of a smiling customer" style="left:24px;top:798px;width:62px;height:60px;background:linear-gradient(180deg,#d8dde0,#b59a82 55%,#3fa8c8 85%)"></div>
  <svg class="abs" style="left:86px;top:815px" width="10" height="24" viewBox="0 0 10 24"><path d="M0 0 L10 12 L0 24" fill="none" stroke="#ddd"/></svg>
  <svg class="abs" style="left:106px;top:806px" width="13" height="10" viewBox="0 0 13 10"><path fill="#888" d="M0 10V5C0 2 2 0 5 0v2C3 2 2.5 3 2.5 4.5H5V10zM7 10V5c0-3 2-5 5-5v2c-2 0-2.5 1-2.5 2.5H12V10z"/></svg>
  <p class="abs quote" style="left:105px;top:822px">This is a powerful and fun to work with premium Sitecraft theme. Carefully handcrafted and designed with ease of use, functionality and flexibility in mind. Take a moment to explore its features on this live preview demo website.</p>

  <h2 class="abs section-title" style="left:336px;width:258px;top:768px">Discount Section<span class="rule"></span></h2>
  <div class="abs" style="left:340px;top:802px;width:45px;height:41px;border:2px solid var(--orange);display:flex;align-items:center;justify-content:center">
    <svg width="22" height="22" viewBox="0 0 24 24"><path fill="var(--navy)" d="M3 12 12 3h8v8l-9 9z"/><circle cx="16.5" cy="7.5" r="1.5" fill="#fff"/><text x="9" y="15" font-size="7" fill="#fff" font-family="Open Sans,sans-serif" font-weight="700">%</text></svg>
  </div>
  <p class="abs disc-text" style="left:398px;top:801px">Lorem Ipsum est simplement du faux exte mployé dans la ion et la misen page avant impression...dans la ion et la misen page avant impression...</p>
  <div class="abs btn-navy" style="left:340px;top:858px;width:92px;height:18px">Get Discount Here</div>

  <h2 class="abs section-title" style="top:934px"><span class="rule"></span>Latest News<span class="rule"></span></h2>

  <article class="abs news" style="left:23px;top:967px;width:186px">
    <div role="img" aria-label="Pound sterling banknotes" style="height:71px;background:linear-gradient(135deg,#c9a3a8,#e6d6d0 45%,#8c8fa6)"></div>
    <div style="display:flex;gap:13px;margin-top:8px">
      <div class="news-icon" style="background:var(--navy)"><svg width="14" height="14" viewBox="0 0 16 16"><path d="M5 1l3 3 3-3M2 4h12v10H2z" fill="none" stroke="#fff"/><path d="M5 7h6M5 9h6M5 11h6" stroke="#fff"/></svg></div>
      <div><h4>Lorem Ipsum est simplement</h4><div class="meta">Dec 12,2013 | by Ellis | 13 Comments</div><p>Lorem Ipsum est simplement du faux exte<br><span class="more">More&gt;&gt;</span></p></div>
    </div>
  </article>
  <article class="abs news" style="left:219px;top:967px;width:187px">
    <div role="img" aria-label="US dollar banknotes close up" style="height:71px;background:linear-gradient(135deg,#5f6a5c,#c9cbbd 50%,#4e574c)"></div>
    <div style="display:flex;gap:13px;margin-top:8px">
      <div class="news-icon" style="background:var(--orange)"><svg width="14" height="14" viewBox="0 0 16 16"><path d="M5 1l3 3 3-3M2 4h12v10H2z" fill="none" stroke="#fff"/><path d="M5 7h6M5 9h6M5 11h6" stroke="#fff"/></svg></div>
      <div><h4>Lorem Ipsum est simplement</h4><div class="meta alt">Dec 12,2013 | by Ellis | 13 Comments</div><p>Lorem Ipsum est simplement du faux exte<br><span class="more alt">More&gt;&gt;</span></p></div>
    </div>
  </article>
  <article class="abs news" style="left:416px;top:967px;width:186px">
    <div role="img" aria-label="Stacks of bundled dollar bills" style="height:71px;background:linear-gradient(135deg,#b7c0a0,#e9e6cf 50%,#9aa583)"></div>
    <div style="display:flex;gap:13px;margin-top:8px">
      <div class="news-icon" style="background:var(--navy)"><svg width="14" height="14" viewBox="0 0 16 16"><path d="M5 1l3 3 3-3M2 4h12v10H2z" fill="none" stroke="#fff"/><path d="M5 7h6M5 9h6M5 11h6" stroke="#fff"/></svg></div>
      <div><h4>Lorem Ipsum est simplement</h4><div class="meta">Dec 12,2013 | by Ellis | 13 Comments</div><p>Lorem Ipsum est simplement du faux exte<br><span class="more">More&gt;&gt;</span></p></div>
    </div>
  </article>

  <footer class="abs footer">
    <div class="abs links"><span>Home</span><span>About Us</span><span>Portfolio</span><span>Services</span><span>Contact</span></div>
    <div class="abs socials"><span style="background:#c8232c"></span><span style="background:#3b5998"></span><span style="background:#3ea9dd"></span><span style="background:#6b6b6b"></span></div>
    <div class="abs copy">Copyright © 2013 Norvane Exchange ltd All Rights Reserved</div>
    <div class="abs legal"><span>Terms &amp; Condition</span><span>|</span><span>Privacy Policy</span></div>
  </footer>
</div>
</body>
</html>
```